quickdeedsale.com redesign with wireframes, white space and custom form are very important

Need a new two column design that will convert easily to mobile responsive. Lots of white space. Winning design will probably be based on header area and making the custom form stand out. I want the header to be very much like www.tallgatevk.com except the form not to go up into the header.
Here are some of the websites I really like:
www.birchdwell.com
http://ourplotpurchasedirect.com/
http://kellbrightproperty.com/

We buy homes for cash and close fast. Our target is a home seller who is desperate to sell quickly.
I have uploaded my really ugly wireframe and my logo. I also uploaded my photo for the about us box and a possible photo to use for the header.
The copy on the wireframe is what I will be using except for the about us box.

Here is the exact link for video to frame in the top left box.
https://clipvault.example/Qm38pzrtLa

0592cd
85cae6
eaf1f7
fbee3d
ec1f27

• Everything on wireframe.
• Must use Verdana font and nothing should be smaller than 12 point. Most should be in 14 point. (except maybe inside of form)

```html
<!DOCTYPE html>
<html lang="en">
<head>
<meta charset="utf-8">
<title>quickdeedsale.com – Sell your home for cash</title>
<link rel="stylesheet" href="https://fonts.googleapis.com/css2?family=Noto+Sans:wght@400;700&display=swap">
<style>
:root{
  --blue:#0592cd;
  --blue-deep:#1479c0;
  --sky:#85cae6;
  --pale:#eaf1f7;
  --yellow:#fbee3d;
  --red:#ec1f27;
  --red-deep:#e2001a;
  --ink:#222;
  --muted:#444;
  --white:#fff;
}
*{box-sizing:border-box;margin:0;padding:0}
html,body{width:1200px;height:2821px;overflow:hidden}
body{font-family:Verdana,"Noto Sans",sans-serif;color:var(--ink);background:linear-gradient(180deg,#dfeaf4 0%,var(--pale) 40%,#e6eef6 100%);position:relative}
.abs{position:absolute}
a{color:inherit;text-decoration:none}

/* header */
.site-header{left:0;top:0;width:1200px;height:103px;background:var(--white)}
.brand{left:128px;top:44px;display:flex;align-items:center;gap:6px;font-weight:700;font-size:13px;line-height:16px;color:var(--red);white-space:nowrap}
.brand-mark{width:14px;height:14px;background:var(--red);flex:none}
.main-nav{top:48px;font-size:15px;font-weight:700;color:#111}
.main-nav a{position:absolute;white-space:nowrap}
.main-nav .active{color:var(--red)}
.header-call{left:884px;top:36px;text-align:right;width:180px}
.header-call small{display:block;font-size:12px;color:#111}
.header-call strong{display:block;font-size:27px;color:var(--red);margin-top:2px;letter-spacing:.5px}

/* hero */
.hero{left:0;top:103px;width:1200px;height:452px;background:linear-gradient(180deg,#5f86b8 0%,#8fb0d6 30%,#3f6b3a 58%,#d9d3c6 72%,#2f4a25 100%)}
.hero-dots{left:574px;top:133px;display:flex;gap:8px}
.hero-dots span{width:8px;height:8px;border-radius:50%;background:var(--white)}
.hero-dots span:first-child{background:#111}
.hero-title{left:0;top:198px;width:1200px;text-align:center;color:var(--white);font-size:22px;font-weight:700;line-height:30px;text-shadow:0 1px 3px rgba(0,0,0,.4)}

/* benefits */
.benefits-title{left:128px;top:632px;font-size:16px;font-weight:700;color:var(--blue)}
.benefits-list{left:128px;top:670px;list-style:none;font-size:12px;color:#222}
.benefits-list li{display:flex;align-items:center;gap:14px;height:25px}
.video-kicker{left:128px;top:793px;font-size:16px;font-weight:700;color:var(--blue)}
.video-title{left:128px;top:810px;font-size:28px;font-weight:700;color:var(--red)}
.video-frame{left:128px;top:862px;width:545px;height:268px;background:var(--white);padding:4px}
.video-frame .poster{width:100%;height:100%;background:linear-gradient(120deg,#6f8b5a 0%,#c9ced1 40%,#4a6f95 60%,#d8dde0 100%);position:relative}
.play{position:absolute;left:240px;top:100px}

/* form */
.lead-form{left:694px;top:602px;width:376px;height:527px;border-radius:12px;overflow:hidden;background:var(--yellow)}
.lead-form-head{height:109px;background:var(--red-deep);padding:16px 23px;color:var(--white)}
.lead-form-head h2{font-size:25px;line-height:28px}
.lead-form-head p{font-size:11px;font-style:italic;margin-top:6px}
.field{position:absolute;left:23px;width:331px;height:32px;background:var(--white);border:0;font-size:10px;color:#999;padding:0 8px;line-height:32px}
.submit{position:absolute;left:23px;top:427px;width:126px;height:31px;background:var(--blue);color:var(--white);font-size:12px;font-weight:700;border:0;text-align:center;line-height:31px}
.submit-note{position:absolute;left:164px;top:434px;font-size:11px}
.privacy-row{position:absolute;left:23px;top:466px;display:flex;align-items:center;gap:9px;font-size:10px}
.privacy-row span.dot{width:24px;height:24px;border-radius:50%;border:2px solid var(--red);background:var(--yellow)}
.privacy-row span.dot:nth-of-type(3){border-color:var(--blue)}
.privacy-row span.dot:nth-of-type(4){border-color:#b58a00}
.privacy-row .label{margin-right:18px}
.call-line{position:absolute;left:23px;top:500px;font-size:12px}

/* intro */
.intro-title{left:128px;top:1186px;width:545px;font-size:21px;line-height:25px;color:var(--red);font-weight:700}
.intro-text{left:128px;top:1296px;width:545px;font-size:14px;line-height:22px;color:var(--muted)}

/* testimonials */
.testimonials{left:694px;top:1166px;width:376px;height:236px;border-radius:12px;background:var(--blue-deep);color:var(--white);padding:18px 18px}
.testimonials h3{font-size:21px;color:var(--yellow)}
.testimonials .quote-mark{font-size:28px;font-weight:700;line-height:16px;margin-top:8px}
.testimonials p{font-size:13px;line-height:21px;margin-top:4px}
.testimonials cite{display:block;font-style:normal;font-weight:700;font-size:13px;margin-top:18px}
.more-btn{display:inline-block;margin-top:17px;background:var(--sky);font-size:12px;font-weight:700;padding:9px 13px}

/* reasons */
.reasons{left:128px;top:1433px;width:540px;height:377px;border-radius:12px;background:var(--red-deep);color:var(--white);padding:24px 19px}
.reasons h3{font-size:22px}
.reasons ul{list-style:none;margin-top:18px;font-size:14px}
.reasons li{height:32px;display:flex;align-items:center;gap:16px}
.reasons .help{font-size:21px;font-weight:700;line-height:34px;margin-top:22px}

/* about */
.card{background:var(--white);border-radius:12px}
.about{left:694px;top:1443px;width:376px;height:175px;padding:22px 24px}
.about .portrait{position:absolute;left:24px;top:22px;width:128px;height:128px;border-radius:50%;background:radial-gradient(circle at 50% 45%,#c98d73,#4f3d33)}
.about h3{position:absolute;left:172px;top:24px;font-size:22px;color:var(--blue)}
.about p{position:absolute;left:172px;top:64px;width:185px;font-size:13px;line-height:21px}

/* cities */
.cities{left:694px;top:1663px;width:376px;height:500px;padding:20px 16px}
.cities h3{font-size:21px;line-height:30px;color:var(--blue)}
.cities .lead{font-size:14px;line-height:22px;margin-top:16px}
.cities .list{font-size:12px;line-height:20px;margin-top:12px}

/* blog */
.blog-title{left:128px;top:1862px;font-size:22px;font-weight:700;color:var(--blue)}
.blog-rule{left:128px;top:1901px;width:540px;height:1px;background:#cdd9e4}
.post{left:128px;width:540px;height:142px}
.post .thumb{position:absolute;left:0;top:0;width:207px;height:142px;background:linear-gradient(180deg,#8cb4dc 0%,#a49684 45%,#4f8a37 100%)}
.post h4{position:absolute;left:218px;top:2px;width:320px;font-size:12px;line-height:18px;color:var(--red)}
.post p{position:absolute;left:218px;top:46px;width:320px;font-size:10px;line-height:15px;color:#444}
.post p b{color:#111}

/* showcase */
.showcase{left:694px;top:2201px;width:376px;height:278px;padding:26px 20px}
.showcase .duo{width:336px;height:184px;background:linear-gradient(90deg,#4b9be0 0%,#c6b79b 48%,#8a7b6a 52%,#6f5c49 100%)}
.showcase p{font-size:16px;font-weight:700;color:var(--blue);line-height:22px;margin-top:10px}

/* bottom nav + footer */
.bottom-nav{top:2554px;left:0;width:1200px;font-size:14px;font-weight:700;color:#333}
.bottom-nav a{position:absolute}
.site-footer{left:0;top:2614px;width:1200px;height:207px;background:var(--blue-deep);color:var(--white);font-size:12px;line-height:20px}
.foot-col{position:absolute;top:30px}
.social{position:absolute;left:934px;top:30px}
.social div{display:flex;align-items:center;justify-content:space-between;width:98px;height:40px}
.social span{width:30px;height:30px;border-radius:50%;border:2px solid var(--white)}
.copyright{position:absolute;left:0;top:176px;width:1200px;text-align:center;font-size:12px}
</style>
</head>
<body>

<header class="site-header abs">
  <a class="brand abs" href="#"><span class="brand-mark"></span>quickdeedsale.com</a>
  <nav class="main-nav abs">
    <a class="active" style="left:299px" href="#">Sell Your Home</a>
    <a style="left:438px" href="#">How it works</a>
    <a style="left:560px" href="#">Stop Foreclosure</a>
    <a style="left:711px" href="#">Probate</a>
    <a style="left:795px" href="#">Contact</a>
  </nav>
  <div class="header-call abs"><small>Call Us ! Nights and weekends</small><strong>555-214-7730</strong></div>
</header>

<section class="hero abs" role="img" aria-label="Photo of a single-storey house with a lawn and trees under a blue sky"></section>
<div class="hero-dots abs"><span></span><span></span><span></span><span></span></div>
<h1 class="hero-title abs">Sell your home for cash in 8 days<br>We buy Houses Nationwide.</h1>

<h2 class="benefits-title abs">These are the benefits of selling your home to us</h2>
<ul class="benefits-list abs">
  <li><svg width="12" height="12" viewBox="0 0 12 12"><circle cx="6" cy="6" r="5" fill="none" stroke="#0592cd" stroke-width="1.5"/><path d="M3.5 6l1.8 1.8L8.5 4.5" fill="none" stroke="#0592cd" stroke-width="1.5"/></svg>You pick the closing date</li>
  <li><svg width="12" height="12" viewBox="0 0 12 12"><circle cx="6" cy="6" r="5" fill="none" stroke="#0592cd" stroke-width="1.5"/><path d="M3.5 6l1.8 1.8L8.5 4.5" fill="none" stroke="#0592cd" stroke-width="1.5"/></svg>You pay NO commissions or fees</li>
  <li><svg width="12" height="12" viewBox="0 0 12 12"><circle cx="6" cy="6" r="5" fill="none" stroke="#0592cd" stroke-width="1.5"/><path d="M3.5 6l1.8 1.8L8.5 4.5" fill="none" stroke="#0592cd" stroke-width="1.5"/></svg>You don't have to paint, clean or make repairs</li>
</ul>

<p class="video-kicker abs">Watch to see our president Dale explain</p>
<h2 class="video-title abs">How easy it is to sell to us</h2>
<div class="video-frame abs">
  <div class="poster" role="img" aria-label="Video still of a couple standing in front of a modern white house">
    <svg class="play" width="58" height="58" viewBox="0 0 58 58"><circle cx="29" cy="29" r="27" fill="rgba(255,255,255,.55)"/><path d="M23 18l18 11-18 11z" fill="#fff"/></svg>
  </div>
</div>

<form class="lead-form abs">
  <div class="lead-form-head">
    <h2>Yes, I want to sell<br>my home fast!</h2>
    <p>Get a no obligation written offer in 36 hours</p>
  </div>
  <div class="field" style="top:124px">Your Name</div>
  <div class="field" style="top:167px">Your phone number</div>
  <div class="field" style="top:210px">Your Email Address</div>
  <div class="field" style="top:253px">Property Address including City, State and Zip Code</div>
  <div class="field" style="top:296px">Repairs needed if any</div>
  <div class="field" style="top:339px">Asking price</div>
  <div class="field" style="top:382px">Comments</div>
  <div class="submit">SUBMIT</div>
  <span class="submit-note">To get started selling your home fast.</span>
  <div class="privacy-row"><span class="label">Our Privacy Policy</span><span class="dot"></span><span class="dot"></span><span class="dot"></span></div>
  <p class="call-line"><b>Call Us</b> 8am to 10 pm Eastern time. We answer our phones.</p>
</form>

<h2 class="intro-title abs">Sell your home or house fast for cash to a professional investor company. We buy Houses and close quickly.</h2>
<p class="intro-text abs">Selling a home on your own has never been easier. From Orlando to Greensboro - and all points in between- you can sell your home today without any hassles. Call 1-800-555-0142 or fill out the form below to get a written offer on your home in just 36 hours. Sell today online to people that care.</p>

<aside class="testimonials abs">
  <h3>Home Seller Testimonials</h3>
  <div class="quote-mark">“</div>
  <p>I just wanted to thank you for buying my home in Winter Park. You made it fast and easy and kept me well informed the whole way.</p>
  <cite>Lena Marsh – Winter Park</cite>
  <span class="more-btn">More Testimonials</span>
</aside>

<section class="reasons abs">
  <h3>If you need to sell a home fast because of:</h3>
  <ul>
    <li>›<span>Divorce or Bankruptcy</span></li>
    <li>›<span>Foreclosure</span></li>
    <li>›<span>Landlord problems evictions with tenants okay</span></li>
    <li>›<span>Inherited property in probate</span></li>
    <li>›<span>Termites, mold, flood or fire damage, leaky roof</span></li>
    <li>›<span>Moving or can't afford mortgage payments</span></li>
  </ul>
  <p class="help">We Can Help.<br>We are the fastest home buyers around.</p>
</section>

<aside class="about card abs">
  <div class="portrait" role="img" aria-label="Portrait photo of the company owner"></div>
  <h3>About Us</h3>
  <p>Owned and operated in Orlando Florida since 2001. Oldest Continuous operated website in country.</p>
</aside>

<aside class="cities card abs">
  <h3>Some of the cities where we buy houses. Not all are listed.</h3>
  <p class="lead">These are the cities where we have an affiliate where you can sell a home fast or quickly and we buy homes:</p>
  <p class="list">Orlando Jacksonville Ft Myers Tampa St Pete Gainesville Tallahassee Melbourne West Palm Beach Apopka Deland Kissimmee Lakeland Ocala Chicago Philadelphia Camden Atlanta Valdosta Houston Detroit Phoenix Seattle Tacoma Portland Charlotte Cincinnati San Antonio Harrisburg Virginia Beach Virginia Homes Greensboro Charleston SC Flint Rochester Lake Florida Wilmington Columbia Titusville If you don't see your city, we still probably buy homes there.<br>These are the types of real estate that we buy: We buy nice houses and outdated problem homes. We buy in great neighborhoods and not so nice. We buy block homes and frame homes. We buy<br>Archives</p>
</aside>

<h2 class="blog-title abs">Blog Posts</h2>
<div class="blog-rule abs"></div>

<article class="post abs" style="top:1926px">
  <div class="thumb" role="img" aria-label="Photo of a large suburban family house"></div>
  <h4>Neque porro quisquam est qui dolorem ipsum quia dolor sit amet, consectetur, adipisci velit...</h4>
  <p>Lorem Ipsum is simply dummy text of the printing and typesetting industry. Lorem Ipsum has been the industry's standard dummy text ever since the 1500s, when an unknown printer took a galley of type and scrambled it to make a type specimen book.<b>Read More</b></p>
</article>
<article class="post abs" style="top:2126px">
  <div class="thumb" role="img" aria-label="Photo of a brick two-storey house"></div>
  <h4>Neque porro quisquam est qui dolorem ipsum quia dolor sit amet, consectetur, adipisci velit...</h4>
  <p>Lorem Ipsum is simply dummy text of the printing and typesetting industry. Lorem Ipsum has been the industry's standard dummy text ever since the 1500s, when an unknown printer took a galley of type and scrambled it to make a type specimen book.<b>Read More</b></p>
</article>
<article class="post abs" style="top:2336px">
  <div class="thumb" role="img" aria-label="Photo of a modern house lit at dusk"></div>
  <h4>Neque porro quisquam est qui dolorem ipsum quia dolor sit amet, consectetur, adipisci velit...</h4>
  <p>Lorem Ipsum is simply dummy text of the printing and typesetting industry. Lorem Ipsum has been the industry's standard dummy text ever since the 1500s, when an unknown printer took a galley of type and scrambled it to make a type specimen book.<b>Read More</b></p>
</article>

<aside class="showcase card abs">
  <div class="duo" role="img" aria-label="Side by side photos of a well kept house and a run-down house"></div>
  <p>We buy nice pretty houses and some ugly ones as well.</p>
</aside>

<nav class="bottom-nav abs">
  <a style="left:169px" href="#">Archives</a>
  <a style="left:282px" href="#">Sell my house</a>
  <a style="left:432px" href="#">Fast cash for homes</a>
  <a style="left:625px" href="#">We buy houses</a>
  <a style="left:783px" href="#">Real Estate investor</a>
  <a style="left:974px" href="#">Latest</a>
</nav>

<footer class="site-footer abs">
  <div class="foot-col" style="left:128px">Sell Your Home<br>How it works<br>Stop Foreclosure<br>Probate<br>Contact</div>
  <div class="foot-col" style="left:370px">Terms &amp; Conditions<br>Privacy Policy</div>
  <div class="foot-col" style="left:611px">Quick Deed Sale Office<br>48 Lindenweg<br>10115 Elmstadt<br>Northland<br>Telephone: +00 11 5550199<br>E-mail: hello@quickdeedsale.com</div>
  <div class="social">
    <div>Neighborly<span></span></div>
    <div>Chirpline<span></span></div>
    <div>Worknet<span></span></div>
  </div>
  <p class="copyright">© 2015 Company Name,All Rights Reserved</p>
</footer>

</body>
</html>
```